Corporate website design needed

We need a Contemporary Industrial/Tech/Logistics Website design to match our logistic client's business. Our client consults and build logistics solutions that they manage but they are not a typical 3PL (3rd party logistics company) which is primarily engaged in moving boxes.
PSD file only for now, home and default templates.
COMPANY CHARACTER
DESIGN LOOK AND FEEL
• The design should also be modern and visually well organized — employing a combination of visual devices and info graphics. Keep it light and not too heavy but strong/ professional. And unique.
• The design should go beyond the typical industrial pick and pack 3PL representing [Logistics Company] as a High Tech/IT logistics company.
Some examples although these are not right for this client because they have much more content and present themselves more as a 3pl.
http://www.vobrelink-hub.example/ (More right then wrong - Like this but simplified)
http://www.durmaxfreight.example (Ugly)
http://www.tpwallerton.example (More right then wrong but different focus)
http://www.pelhamrye.example/ Too 3PL trucking… We want a bit ore high level approach
The difference, the design should be a fusion in core concepts that culminate in a design which implies the following attributes. Tech (Big data / analytics / software), Consultancy (Solutions, SME, Leader), 3PL Industry vertical solutions.
NOTE: The visualization of “tech” is not “1” and “0”, but more “software and analytics” Perhaps more like www.navimetra.example.
• They need to be seen as a solutions provider in Logistics and as in Subject matter experts
TONE
The tone needs to exude professionalism, expertise, though leadership along with technical and executional excellence.
Experienced
Knowledgeable
Confident
Determined
Straightforward
WEBSITE OBJECTIVES
• Focus C-Suite executives and logistics managers’ attention on [Logistics Company]s commanding knowledge and expertise, and unique approach to supply chain solutions producing more RFP wins
• Create an easy to scan design which decreases the reliance on text through featured text, summaries, and smaller “chunked” size bits of information.
• Convey [Logistics Company] as high-tech 3PL solutions developer and services provider with a ‘high-touch’ consultative approach.
• Showcase [Logistics Company]’s value propositions. (See Slider Content)
• Showcase [Logistics Company]’s expertise in logistical analytics.
• Gain recognition as an industry leader in evolutionary new space (supply chain 2.0)
WEBSITE STRATEGY
• Reduce reliance on text (at least within initial entry points for each section)
• Typography: Watch text line lengths and readability, bolder fonts. NO SERIFS
• Generally, create a click-through format so that users who want more details can find it, and those who don’t can get a snapshot without clicking through.
• Increase visual content through info graphics and some dynamic content, photography
• Better utilize the space on each page (e.g., add visual interest, photography and iconography where appropriate to break up copy blocks and maintain readable line lengths).
COLOR SCHEME
• Create a more engaging color scheme (the logo will remain the same under all circumstances).
• Red / grayscale may work…. Not too dark or heavy. Not too much red. Ex. quiltora.example
• Also try blues and greys. They seem to like that. Open to suggestions but don’t get to crazy. Red is in their logo but too much may be a problem.
PHOTOGRAPHY
Yes. And I will upload some.
If you pick photography please be sure to note Which stock house used and the image number!
CONTENT
The content will be presented in a more hierarchical format — with lead-ins, paragraph and section headers and navigational cues to expand lengthier content allowing the visitor to more easily scan the website. No case studies, No Social media, News while on the home page should not be over emphasized. They don't post a lot so it gets dated quickly ...
I will be uploading a wire frame and other elements.
NOTE: I uploaded my EXAMPLE mock up which is close but not close enough.
I am not a great designer. So I am looking for an alternative that exceed my design ability! These examples show the basic layout but I really want some varied alternatives.
The colors are inconsistent and type not quite right. The grey bar at top is not right and should probably go away.
Please pull the basic elements in the example together into a great design.
If you have questions please contact me.
i will upload some photography tomorrow that may be of use.
Thanks!
Updates
Hi All,
We are still evaluating the submitted designs. Sorry for the delay.
Target Market(s)
This website is primarily a validation website. Few new customers will search and find them as such...
The site should be Focused on C-Suite executives and logistics managers’ attention on [Logistics Company]s commanding knowledge and expertise, and unique approach to supply chain solutions producing more RFP wins
Industry/Entity Type
Business
Font styles to use
Requirements
Must have
- Slide show, Clearly explain who they are and what they do.
Create an easy to scan design which decreases the reliance on text through featured text, summaries, and smaller “chunked” size bits of information.
Convey [Logistics Company] as high-tech 3PL solutions developer and services
provider with a ‘high-touch’ consultative approach.
Should not have
- No Ads space
No Social media
Not too cluttered. Keep it clean.

```html
<!DOCTYPE html>
<html lang="en">
<head>
<meta charset="utf-8">
<title>Keystride Logistics</title>
<link href="https://fonts.googleapis.com/css2?family=Open+Sans:ital,wght@0,400;0,600;0,700;1,400;1,600&family=Ubuntu:wght@400;500;700&display=swap" rel="stylesheet">
<style>
:root{
  --red:#c8102e;
  --red-dark:#9e0c22;
  --ink:#2c2c2c;
  --text:#555;
  --muted:#888;
  --line:#dcdcdc;
  --paper:#ffffff;
  --panel:#f1f1f1;
  --topbar:#3a3a3a;
  --band:#2f3b4a;
  --footer:#262626;
  --footer-text:#b5b5b5;
}
*{box-sizing:border-box;margin:0;padding:0}
html,body{width:783px;height:1200px;overflow:hidden}
body{font-family:"Open Sans",Arial,sans-serif;color:var(--text);background:var(--paper);font-size:7px;line-height:1.45}
h2,h3,.nav a,.hero-title{font-family:"Ubuntu","Open Sans",sans-serif}
a{color:inherit;text-decoration:none}

.topbar{height:14px;display:flex;justify-content:flex-end}
.topbar-links{background:var(--topbar);color:#ddd;font-size:6.5px;padding:2px 14px;display:flex;gap:8px;align-items:center}
.topbar-links .sales{color:#fff;font-weight:600}

.header{height:86px;display:flex;justify-content:space-between;align-items:flex-end;padding:0 40px 8px 56px;border-bottom:3px solid var(--red)}
.brand{display:flex;align-items:center;gap:8px;padding-bottom:6px}
.brand-dot{width:26px;height:26px;border-radius:50%;background:var(--red)}
.brand-name{font-family:"Open Sans",sans-serif;font-weight:700;font-size:17px;color:var(--ink);letter-spacing:.5px;line-height:1.1}
.nav{display:flex;gap:2px}
.nav a{font-size:8px;font-weight:500;color:var(--ink);padding:6px 14px;letter-spacing:.3px}
.nav a.active{background:var(--red);color:#fff}

.hero{position:relative;height:298px;background:linear-gradient(100deg,#c9ccd0 0%,#9aa1a8 45%,#6d747c 100%)}
.hero-photo{position:absolute;inset:0}
.hero-copy{position:absolute;left:96px;top:86px}
.hero-title{display:inline-block;background:rgba(60,60,60,.85);color:#fff;font-size:22px;font-weight:500;padding:4px 12px}
.hero-sub{display:block;margin-top:4px;width:max-content;background:rgba(255,255,255,.9);color:var(--ink);font-size:12px;padding:4px 12px}
.hero-arrow{position:absolute;top:134px;width:22px;height:30px;background:rgba(40,40,40,.7);display:flex;align-items:center;justify-content:center}
.hero-arrow.left{left:0}.hero-arrow.right{right:0}

.lead-band{background:var(--band);color:#fff;font-style:italic;font-size:11.5px;line-height:1.5;text-align:center;padding:12px 70px;height:70px}

.section-title{font-size:13px;font-weight:700;color:var(--ink);position:relative;padding-bottom:4px;display:inline-block}
.section-title::after{content:"";position:absolute;left:0;bottom:0;width:26px;height:2px;background:var(--red)}
.section-title .accent{color:var(--red)}

.services{position:relative;padding:12px 56px 0;height:170px}
.services-grid{display:grid;grid-template-columns:repeat(4,1fr);gap:24px;margin-top:12px}
.service-head{display:flex;gap:8px;align-items:center;height:34px}
.service-icon{width:30px;height:30px;background:var(--red);flex:none;display:flex;align-items:center;justify-content:center}
.service-head h3{font-size:8px;font-weight:700;color:var(--ink);line-height:1.25}
.service p{margin-top:8px;font-size:6.5px;color:var(--muted)}
.read-more{display:block;text-align:right;color:var(--red);font-size:6.5px;font-weight:600;margin-top:4px}
.services-arrow{position:absolute;top:96px;font-size:16px;color:var(--muted)}
.services-arrow.left{left:20px}.services-arrow.right{right:20px}

.triptych{background:var(--panel);border-top:1px solid var(--line);height:232px;padding:14px 56px 0;display:grid;grid-template-columns:repeat(3,1fr);gap:24px}
.triptych h2{margin-bottom:10px}
.media{height:94px;margin-bottom:8px}
.media.process{background:linear-gradient(135deg,#fafafa,#d8dde3)}
.media.video{background:linear-gradient(135deg,#7e8590,#3e4650)}
.media.difference{background:linear-gradient(180deg,#5b1a22,#9e1a2b 55%,#4a4a4a)}
.process-list{list-style:none;font-size:7px;color:var(--text)}
.process-list li::before{content:"→ ";color:var(--red)}
.triptych p{font-size:6.5px;color:var(--muted)}

.feature-news{height:156px;padding:14px 56px 0;display:grid;grid-template-columns:1fr 1fr;gap:36px}
.feature-body{display:flex;gap:10px;margin-top:12px}
.feature-photo{width:120px;height:84px;flex:none;background:linear-gradient(160deg,#8fb0cf,#b08a6a)}
.feature-body p{font-size:6.5px;color:var(--muted)}
.news-item{display:flex;gap:8px;margin-top:12px}
.news-date{width:24px;height:24px;background:var(--red);flex:none;color:#fff;font-size:6px;font-weight:700;text-align:center;line-height:1.1;padding-top:5px}
.news-item h3{font-size:7.5px;font-weight:700;color:var(--ink)}
.news-item p{font-size:6.5px;color:var(--muted)}

.footer{background:var(--footer);height:148px;padding:16px 56px 0;display:grid;grid-template-columns:1fr 1fr 1fr 1fr 110px;gap:14px;color:var(--footer-text)}
.footer h3{font-size:8px;color:#fff;font-weight:700;margin-bottom:6px}
.footer ul{list-style:none;font-size:6.5px;line-height:1.55}
.footer-brand{display:flex;align-items:center;gap:6px;padding-top:8px}
.footer-brand .brand-dot{width:20px;height:20px}
.footer-brand .brand-name{color:#fff;font-size:11px}
.copyright{background:var(--red);color:#fff;height:18px;font-size:6.5px;text-align:center;line-height:18px}
</style>
</head>
<body>
<div class="topbar">
  <div class="topbar-links"><a href="#">COMPANY</a>|<a href="#">CAREERS</a>|<a href="#">CONTACT</a>|<span>Search</span>|<span class="sales">Sales: 800-555-0142</span></div>
</div>

<header class="header">
  <div class="brand"><span class="brand-dot"></span><span class="brand-name">KEYSTRIDE<br>LOGISTICS</span></div>
  <nav class="nav"><a class="active" href="#">SOLUTIONS ▾</a><a href="#">OUR PROCESS ▾</a><a href="#">INDUSTRIES ▾</a></nav>
</header>

<section class="hero">
  <div class="hero-photo" role="img" aria-label="Executive touching a digital analytics interface in a grey, high-tech setting"></div>
  <div class="hero-copy">
    <span class="hero-title">A New Way to Think</span>
    <span class="hero-sub">about supply chain transformation</span>
  </div>
  <a class="hero-arrow left" href="#"><svg width="8" height="12" viewBox="0 0 8 12"><path d="M7 1L2 6l5 5" stroke="#fff" stroke-width="2" fill="none"/></svg></a>
  <a class="hero-arrow right" href="#"><svg width="8" height="12" viewBox="0 0 8 12"><path d="M1 1l5 5-5 5" stroke="#fff" stroke-width="2" fill="none"/></svg></a>
</section>

<div class="lead-band">Keystride manages complexity, provides data-driven solutions and implements innovative and actionable strategies that delivers business results.</div>

<section class="services">
  <h2 class="section-title">Our Services</h2>
  <div class="services-grid">
    <div class="service">
      <div class="service-head"><span class="service-icon"><svg width="16" height="16" viewBox="0 0 16 16"><rect x="2" y="4" width="12" height="9" fill="none" stroke="#fff" stroke-width="1.5"/><path d="M2 7h12" stroke="#fff" stroke-width="1.5"/></svg></span><h3>Material Management &amp; Industry Support</h3></div>
      <p>We plan, source and control materials so your lines keep moving and inventory stays lean across every site.</p>
      <a class="read-more" href="#">Read More ›</a>
    </div>
    <div class="service">
      <div class="service-head"><span class="service-icon"><svg width="16" height="16" viewBox="0 0 16 16"><path d="M2 3h2l2 7h7l1-5H5" fill="none" stroke="#fff" stroke-width="1.5"/><circle cx="7" cy="13" r="1.2" fill="#fff"/><circle cx="12" cy="13" r="1.2" fill="#fff"/></svg></span><h3>Retail and e-Commerce Distribution</h3></div>
      <p>Fast, accurate order flow for stores and online shoppers, built on clear data and flexible network design.</p>
      <a class="read-more" href="#">Read More ›</a>
    </div>
    <div class="service">
      <div class="service-head"><span class="service-icon"><svg width="16" height="16" viewBox="0 0 16 16"><circle cx="8" cy="8" r="5" fill="none" stroke="#fff" stroke-width="1.5"/><path d="M8 5v3l2 2" stroke="#fff" stroke-width="1.5" fill="none"/></svg></span><h3>Aftermarket Support</h3></div>
      <p>Parts, returns and repair flows managed end to end to protect uptime and lift customer loyalty.</p>
      <a class="read-more" href="#">Read More ›</a>
    </div>
    <div class="service">
      <div class="service-head"><span class="service-icon"><svg width="16" height="16" viewBox="0 0 16 16"><path d="M8 2l6 11H2z" fill="none" stroke="#fff" stroke-width="1.5"/><path d="M8 6v4" stroke="#fff" stroke-width="1.5"/></svg></span><h3>Critical Logistics</h3></div>
      <p>Time-sensitive shipments handled with precision, visibility and a team ready around the clock.</p>
      <a class="read-more" href="#">Read More ›</a>
    </div>
  </div>
  <span class="services-arrow left">‹</span><span class="services-arrow right">›</span>
</section>

<section class="triptych">
  <div>
    <h2 class="section-title">Our <span class="accent">Process</span></h2>
    <div class="media process" role="img" aria-label="Circular supply chain process diagram"></div>
    <ul class="process-list"><li>Concept of operations</li><li>Supplying the infrastructure</li></ul>
    <a class="read-more" href="#">Read More ›</a>
  </div>
  <div>
    <h2 class="section-title">Introduction <span class="accent">Video</span></h2>
    <div class="media video" role="img" aria-label="Video still of a business team meeting"></div>
    <p>See how our analysts and engineers design supply chain solutions that turn complex data into clear, measurable results for clients.</p>
    <a class="read-more" href="#">Read More ›</a>
  </div>
  <div>
    <h2 class="section-title">The Keystride <span class="accent">Difference</span></h2>
    <div class="media difference" role="img" aria-label="Graphic reading Delivering real business growth and Responsive implementation"></div>
    <p>We combine deep industry expertise with software and analytics to deliver responsive implementation and real business growth.</p>
    <a class="read-more" href="#">Read More ›</a>
  </div>
</section>

<section class="feature-news">
  <div>
    <h2 class="section-title">Featured Industry</h2>
    <div class="feature-body">
      <div class="feature-photo" role="img" aria-label="Modern retail storefront building"></div>
      <p>Our retail and e-commerce solutions help store chains and online sellers balance inventory, speed up delivery and respond to shifting demand with confidence and control.<br><a class="read-more" href="#">Read More ›</a></p>
    </div>
  </div>
  <div>
    <h2 class="section-title">Latest <span class="accent">News</span></h2>
    <div class="news-item"><span class="news-date">12<br>MAY</span><div><h3>New analytics center opens</h3><p>Our team expands data services to support growing client networks.</p></div></div>
    <div class="news-item"><span class="news-date">03<br>APR</span><div><h3>Leadership joins industry panel</h3><p>Experts share views on supply chain 2.0 and smarter planning.</p></div></div>
  </div>
</section>

<footer class="footer">
  <div><h3>Our Process</h3><ul><li>Concept of operations</li><li>Supplying the infrastructure</li><li>Analyzing the data</li><li>Managing complexity</li><li>Providing actionable strategies</li><li>Investing in our client's success</li><li>Driving business results</li></ul></div>
  <div><h3>Our Solutions</h3><ul><li>Business Analytics</li><li>Geographic Coverage</li><li>Project Financing</li><li>Project Implementation</li><li>Technology</li><li>Quality</li></ul></div>
  <div><h3>Industries We Serve</h3><ul><li>Aerospace</li><li>Defense</li><li>Industrial</li><li>Manufacturing</li><li>Media and Entertainment</li><li>Medical</li><li>Retail</li><li>Telecom and Electronics</li></ul></div>
  <div><h3>Company</h3><ul><li>Culture</li><li>Community Involvement</li><li>Metrics Process</li><li>Careers</li><li>Contact</li></ul></div>
  <div class="footer-brand"><span class="brand-dot"></span><span class="brand-name">KEYSTRIDE<br>LOGISTICS</span></div>
</footer>
<div class="copyright">Copyright © 2014 Keystride Logistics. All Rights Reserved</div>
</body>
</html>
```